Dog Snacks brand needs a new packaging design

Dear Designers,

We are looking for a packaging expert to design our new line of Dog Snacks which contain a relaxing hemp extract (CBD).

Our company is already selling various relaxing cat & dog products , and we would like this new design to reflect the same "style & feeling" as our current products (see attached instructions).

Technical aspects:
- The packaging is a Stand Up Pouch (12x18.5x7cm - see attached instructions).
- Please follow technical guidelines from printer (see attached instructions).
- The packaging will contain 120g of high-quality, semi-moist dog snacks.
- We will be designing 3 differents variations for 3 different flavours: Chicken, Beef & Liver.
- The packaging will be printed with a matt finish.

Design aspects:
- The design should be compatible with our brand identity (i.e. fluffly, pure, relaxing, positive, clean & natural).
- Soft/rounded shapes are preferred.
- Please use our brand's colors (#3BA384, White & Black).
- Please use our company logo (see attached instructions).
- The design also needs to convey a strong sense of professionalism as we are an animal "healthcare" brand.
- If you want to include a dog picture, we would prefer you to use a picture of our official brand ambassador (see attached instructions).
- We have attached a number of packaging examples which we like a lot. (see attached instructions). Please only use those as general inspiration.
- Only original work (no plagiarism will be accepted).

Please don't hesitate to send us a message if you have any questions about the brand, the product or the design requirements.

We look forward to seeing your designs & working on this together !

Thanks & regards,
Tobias

Target Market(s)

Dog owners

Industry/Entity Type

Pet Care

Font styles to use
Sans Serif

Requirements
Must have
• Please see project description.
Nice to have
Should not have

```html
<!DOCTYPE html>
<html lang="en">
<head>
<meta charset="utf-8">
<title>Relaxing Treats – Pouch Front</title>
<link rel="stylesheet" href="https://fonts.googleapis.com/css2?family=Montserrat:wght@500;600;700;800&family=Oswald:wght@300;400;500&display=swap">
<style>
  :root {
    --backdrop: #0b7357;
    --brand-green: #3ba384;
    --deep-green: #1f7d61;
    --mint: #9fd3c0;
    --pale-mint: #e4f2ec;
    --white: #ffffff;
    --ink: #111a16;
    --chicken: #c67f22;
    --biscuit: #b79354;
  }
  * { box-sizing: border-box; margin: 0; padding: 0; }
  html, body { width: 1200px; height: 835px; overflow: hidden; background: var(--backdrop); }
  .canvas { position: relative; width: 1200px; height: 835px; }

  .pouch {
    position: absolute; left: 385px; top: 38px; width: 430px; height: 760px;
    background: linear-gradient(180deg, #f6f8f7 0%, var(--white) 40%, #f4f6f5 100%);
    border-radius: 10px 10px 14px 14px;
    overflow: hidden;
    font-family: "Montserrat", sans-serif;
    color: var(--ink);
  }
  .top-bands { position: absolute; left: 0; top: 40px; width: 430px; height: 60px; }

  .brand { position: absolute; left: 0; width: 430px; top: 168px; text-align: center; }
  .brand-name { font-size: 27px; font-weight: 600; letter-spacing: 1px; color: var(--ink); }
  .brand-tagline {
    position: absolute; right: 142px; top: 34px;
    font-size: 11px; font-weight: 500; color: var(--brand-green); letter-spacing: .3px;
  }

  .badge {
    position: absolute; left: 327px; width: 66px; height: 66px; border-radius: 50%;
    border: 1.5px solid var(--brand-green);
    box-shadow: inset 0 0 0 6px var(--white), inset 0 0 0 7px var(--mint);
  }
  .badge.one { top: 100px; }
  .badge.two { top: 182px; }
  .badge.three { top: 262px; }

  .headline { position: absolute; left: 34px; top: 290px; line-height: 1; }
  .headline-main { font-size: 49px; font-weight: 800; color: var(--deep-green); letter-spacing: -.5px; }
  .headline-sub { margin-top: 6px; margin-left: 7px; font-size: 40px; font-weight: 700; letter-spacing: 5px; color: var(--ink); }

  .rule { position: absolute; height: 2px; background: var(--deep-green); left: 44px; }
  .rule.upper { top: 407px; width: 152px; }
  .rule.lower { top: 456px; width: 128px; }
  .dose { position: absolute; left: 44px; top: 421px; font-size: 19px; font-weight: 700; color: var(--ink); }

  .audience {
    position: absolute; left: 47px; top: 480px;
    font-family: "Oswald", sans-serif; font-weight: 300; font-size: 16px; line-height: 1.15; color: var(--ink);
  }
  .audience-icon {
    position: absolute; left: 106px; top: 483px; width: 46px; height: 42px;
    background: var(--deep-green); opacity: .85; border-radius: 8px;
  }

  .photo-window { position: absolute; left: 0; top: 0; width: 430px; height: 760px; }

  .flavour {
    position: absolute; left: 45px; top: 555px; width: 80px; height: 80px; border-radius: 50%;
    background: var(--chicken);
    box-shadow: inset 0 0 0 5px var(--chicken), inset 0 0 0 6.5px #f3d9b0;
    font-family: "Oswald", sans-serif; color: var(--white); text-align: center;
    display: flex; flex-direction: column; justify-content: center; line-height: 1;
  }
  .flavour-main { font-size: 14px; font-weight: 500; }
  .flavour-sub { font-size: 11px; font-weight: 300; margin-top: 2px; }
  .treat-art {
    position: absolute; left: 120px; top: 562px; width: 58px; height: 78px;
    background: linear-gradient(160deg, #c9a868, var(--biscuit)); border-radius: 16px;
  }

  .footer-band {
    position: absolute; left: 0; bottom: 0; width: 430px; height: 74px;
    background: linear-gradient(180deg, #8cc8b2 0%, var(--brand-green) 40%, #7bbfa7 100%);
  }
  .sub-brand {
    position: absolute; left: 114px; top: 638px; z-index: 2;
    font-family: "Oswald", sans-serif; font-weight: 300; font-size: 41px; line-height: 1.1; color: var(--brand-green);
  }
  .sub-brand sup { font-size: 10px; vertical-align: top; position: relative; top: 2px; margin-left: 2px; }
  .footer-claims {
    position: absolute; left: 0; width: 430px; bottom: 32px; text-align: center; z-index: 2;
    font-size: 10.5px; font-weight: 600; letter-spacing: 2.6px; color: var(--white);
  }
</style>
</head>
<body>
<div class="canvas">
  <div class="pouch">
    <svg class="top-bands" viewBox="0 0 430 60" aria-hidden="true">
      <path d="M0 14 H175 Q203 14 215 40 Q227 14 255 14 H430" fill="none" stroke="#3ba384" stroke-width="7"/>
      <path d="M0 30 H185 Q205 30 215 50 Q225 30 245 30 H430" fill="none" stroke="#9fd3c0" stroke-width="4"/>
    </svg>

    <div class="brand">
      <div class="brand-name">VERDALO</div>
      <div class="brand-tagline">For Animals</div>
    </div>

    <div class="badge one"></div>
    <div class="badge two"></div>
    <div class="badge three"></div>

    <div class="headline">
      <div class="headline-main">RELAXING</div>
      <div class="headline-sub">TREATS</div>
    </div>

    <div class="rule upper"></div>
    <div class="dose">CBD 250MG</div>
    <div class="rule lower"></div>

    <div class="audience">For dogs<br>of all sizes</div>
    <div class="audience-icon" role="img" aria-label="Small silhouette of a large and a small dog"></div>

    <svg class="photo-window" viewBox="0 0 430 760" role="img" aria-label="Photo of the brand's white wrinkled dog with a blue butterfly on its nose">
      <defs>
        <linearGradient id="photoTone" x1="0" y1="0" x2="1" y2="1">
          <stop offset="0" stop-color="#eeeeee"/>
          <stop offset=".6" stop-color="#dcd6d2"/>
          <stop offset="1" stop-color="#c9c2be"/>
        </linearGradient>
        <linearGradient id="photoFade" x1="0" y1="0" x2="0" y2="1">
          <stop offset="0" stop-color="#fff"/>
          <stop offset=".85" stop-color="#fff"/>
          <stop offset="1" stop-color="#fff" stop-opacity="0"/>
        </linearGradient>
        <mask id="photoMask">
          <rect x="0" y="0" width="430" height="648" fill="url(#photoFade)"/>
        </mask>
      </defs>
      <g mask="url(#photoMask)">
        <circle cx="430" cy="640" r="262" fill="#3ba384"/>
        <circle cx="438" cy="646" r="250" fill="url(#photoTone)"/>
      </g>
    </svg>

    <div class="flavour">
      <span class="flavour-main">CHICKEN</span>
      <span class="flavour-sub">RECIPE</span>
    </div>
    <div class="treat-art" role="img" aria-label="Two bone-shaped chicken biscuits"></div>

    <div class="footer-band"></div>
    <div class="sub-brand">VerdaYum<sup>TM</sup></div>
    <div class="footer-claims">CALMS | SOOTHES | RELAXES</div>
  </div>
</div>
</body>
</html>
```